Chai Tea Company needs a Tea Packaging Box Design

Tea Packaging
Dimensions of the Tea Packaging Box: Height 13 cm; Width 8.5 cm; Depth 7 cm
Individual Teabag Packet/ Sachet: Width 6.5 cm; Length 8.25 cm
We are looking for a new tea packaging design, for our tea business. The material of the box is cardboard. We are also looking for a design that will be on each individual tea bag sachet/packet that goes into the box. This design will be very similar to what you design for the tea packaging box.
Product Info:
Our tea company is called “Velmora Brew”. We sell two types of Chai Tea, once called “Velmora Gold” and one called “Velmora Meadow”. The Velmora Gold has caffeine, while the Velmora Meadow is Naturally Caffeine Free. The Velmora Gold has a black tea base, while the Velmora Meadow has a Rooibos tea base. We will need two tea packaging designs, one for each Chai Tea flavour. The designs for both the teas can be similar, but make sure that you can easily distinguish one from the other (example: make them have different colours or pictures). Both the chai teas, come from the same product line.
Tea Packaging Design:
We are looking for high end tea packaging. We produce high quality teas, and we would like to portray this in our tea packaging. Our teas are made with no artificial flavourings, natural flavourings, or preservatives, so we would also like a natural, organic, high quality look to our tea packaging. Our current logo is a llama. It would be great if you could make the current logo more polished and well made. If you feel that the llama is not well suited or you would like to design the llama differently, we are open to your creative ideas.
General Basic Info:
Keep in mind, we will have both English and French writing on the tea packaging. You do not need to worry about the French writing (we will do the translation), just make sure there is room for it. However, if you feel that you are capable and knowledgeable of incorporating both French and English language into the tea packaging that would be of great help and value.
Back of the Box:
- Will have ingredients and brewing instructions. Basic brewing instructions are: “Add hot water to teabag. Steep for 5-7 minutes, depending on strength preferred. Add milk and your choice of sweetener. Enjoy! See inside panel of box for more detailed instructions”. (The basic brewing instructions, can further be polished or written in a more creative or professional manner).
Front of the Box:
- Will have company name, type of tea, little description of the tea
- 18 teabags
- 54 g (1.9 OZ)
- Should state that this is a product of Alberta, Canada.
Side of the Box:
Any creative wording, slogan, or description about the tea, or whatever you feel would be good on the side of the box.
On the inside flap of the side of the box, there will be detailed instructions on how to brew the tea. These will be different from the simplified brewing instructions on the back of the box. I have attached the advanced brewing instructions as a file. These instructions can further be simplified or reduced to make it easier and cleaner for the consumers to read.
Individual Tea Sachets/ Packets
- These will have a matching look and design of the tea box packaging, except on a smaller scale. Each individual sachet will have the company name, type of tea, little description of the tea in the front of the sachet, while the back will contain the ingredients, and basic brewing instructions.
I have attached a few files, with the dimensions, ingredients, detailed brewing directions, and current logo of the business.
If you have any questions, about the design or packaging please let me know. The winning designer will be required to do a few additional tweaks to finalize the product. Thank you for your time and happy designing!

```html
<!DOCTYPE html>
<html lang="en">
<head>
<meta charset="utf-8">
<title>Velmora Brew – Velmora Gold Tea Box</title>
<link rel="stylesheet" href="https://fonts.googleapis.com/css2?family=Cinzel:wght@400;600;700&family=Playball&display=swap">
<style>
  :root {
    --backdrop: #d6d6d6;
    --kraft: #a68c5b;
    --kraft-dark: #8c7446;
    --label: #f8f7f3;
    --navy: #2c4a5e;
    --slate: #6f93a8;
    --gold: #8a7440;
    --gold-line: #b39a5a;
    --green: #5e8a2c;
    --green-light: #9cc14a;
    --llama-brown: #3a2a1c;
    --llama-blue: #a9c3d3;
  }
  * { box-sizing: border-box; margin: 0; padding: 0; }
  html, body { width: 1200px; height: 1000px; overflow: hidden; }
  body {
    background: var(--backdrop);
    font-family: "Cinzel", serif;
    color: var(--navy);
    position: relative;
  }
  .panel {
    position: absolute;
    top: 210px;
    width: 340px;
    height: 560px;
    background: linear-gradient(180deg, var(--kraft) 0%, var(--kraft-dark) 100%);
    box-shadow: 0 6px 18px rgba(0,0,0,.18);
  }
  .panel--front { left: 60px; }
  .panel--back { left: 430px; }
  .panel--side { left: 800px; }
  .label {
    position: absolute;
    left: 42px; right: 42px; top: 0; bottom: 0;
    background: var(--label);
    display: flex;
    flex-direction: column;
    align-items: center;
    text-align: center;
    padding: 14px 16px;
  }
  .llama-mark { display: block; }
  .brand-name {
    font-family: "Cinzel", serif;
    font-weight: 600;
    color: var(--navy);
    letter-spacing: .5px;
    white-space: nowrap;
  }
  .seal-ribbon { margin: 4px 0 6px; }
  .variety-row {
    display: flex; justify-content: space-between; width: 100%;
    font-size: 10px; font-weight: 600; color: var(--navy);
  }
  .variety-row .sub { font-weight: 400; color: var(--gold); font-size: 8.5px; }
  .product-title {
    font-family: "Playball", cursive;
    font-size: 34px; color: var(--slate);
    line-height: 1; margin: 10px 0 4px;
  }
  .desc-en { font-size: 10px; font-weight: 700; line-height: 1.25; color: var(--navy); }
  .rule { width: 100%; height: 1.5px; background: var(--gold-line); margin: 6px 0; }
  .desc-fr { font-size: 8.5px; line-height: 1.3; color: var(--gold); }
  .count { display: flex; align-items: center; gap: 8px; font-size: 28px; color: var(--gold); line-height: 1; margin-top: 6px; }
  .count .dot { width: 12px; height: 12px; border-radius: 50%; background: var(--green); }
  .small-gold { font-size: 9px; color: var(--gold); line-height: 1.35; }
  .small-gold.big { font-size: 11px; }
  .heading { font-size: 12px; font-weight: 700; color: var(--navy); margin: 6px 0 8px; letter-spacing: .5px; }
  .copy { font-size: 8.5px; line-height: 1.45; color: #5a5a5a; text-align: left; width: 100%; margin-bottom: 8px; }
  .copy.center { text-align: center; }
  .address { font-size: 8px; line-height: 1.35; color: #333; margin-top: 6px; }
</style>
</head>
<body>

  <!-- Front panel -->
  <section class="panel panel--front">
    <div class="label">
      <svg class="llama-mark" width="22" height="26" role="img" aria-label="Small llama brand emblem"><rect width="22" height="26" rx="3" fill="var(--llama-blue)"/></svg>
      <div class="brand-name" style="font-size:11px;margin-top:2px">Velmora Brew</div>
      <svg class="seal-ribbon" width="70" height="30"><rect x="0" y="12" width="70" height="14" fill="var(--green)"/><circle cx="35" cy="14" r="13" fill="#c9b35a"/></svg>
      <div class="variety-row"><span>Chai Tea</span><span style="color:var(--slate)">■</span><span>Thé Chai</span></div>
      <div class="variety-row"><span class="sub">With Caffeine</span><span class="sub">Avec la Caféine</span></div>
      <h1 class="product-title">Velmora Gold</h1>
      <p class="desc-en">An exotic blend of black tea, cardamom, fennel, cloves, ginger and cinnamon</p>
      <div class="rule"></div>
      <p class="desc-fr">Un mélange exotique de thé noir, cardamome, le fenouil, clous de girofle, le gingembre et la cannelle</p>
      <svg width="150" height="140" style="margin:10px 0 6px" role="img" aria-label="Large walking llama silhouette in dark brown tones">
        <defs><linearGradient id="llamaFront" x1="0" y1="0" x2="0" y2="1"><stop offset="0" stop-color="#4a3724"/><stop offset="1" stop-color="var(--llama-brown)"/></linearGradient></defs>
        <rect width="150" height="140" rx="6" fill="url(#llamaFront)"/>
      </svg>
      <div class="brand-name" style="font-size:20px">Velmora Brew</div>
      <div class="count"><span class="dot"></span>18<span class="dot"></span></div>
      <div class="small-gold big">Tea Bags</div>
      <div class="small-gold">Sachets de Thé</div>
      <div class="small-gold" style="font-size:7.5px">No Preservatives &amp; No Artificial Flavors</div>
      <div class="small-gold big">Net Wt 54 g (1.9 oz)</div>
      <div class="small-gold">Product of Alberta, Canada</div>
    </div>
  </section>

  <!-- Back panel -->
  <section class="panel panel--back">
    <div class="label">
      <svg width="40" height="44" style="margin-top:4px"><path d="M20 2 L38 8 V24 C38 34 28 40 20 42 C12 40 2 34 2 24 V8 Z" fill="var(--green-light)" stroke="#c9b35a" stroke-width="2"/></svg>
      <h2 class="heading">Directions</h2>
      <p class="copy">To get the most out of every cup, bring water to boiling and steep 5 to 7 minutes depending on strength preferred.</p>
      <p class="copy">For a stronger tea, use 2 tea bags.</p>
      <p class="copy">Add milk and your choice of sweetener. Enjoy!</p>
      <p class="copy center">*See inside panel of box for more detailed instructions</p>
      <h2 class="heading">Ingredients</h2>
      <p class="copy center">Black Tea, Cardamom, Cloves, Fennel, Ginger, and Cinnamon</p>
      <svg width="90" height="90" style="margin:14px 0 6px" role="img" aria-label="Pale blue llama brand emblem"><rect width="90" height="90" rx="6" fill="var(--llama-blue)"/></svg>
      <div class="brand-name" style="font-size:17px">Velmora Brew</div>
      <p class="address">Box 1187 RPO Northgate<br>Lethbridge, Alberta<br>Canada</p>
      <svg width="30" height="30" style="margin-top:12px"><circle cx="15" cy="15" r="13" fill="none" stroke="var(--green)" stroke-width="2"/></svg>
    </div>
  </section>

  <!-- Side panel -->
  <section class="panel panel--side">
    <div class="label" style="justify-content:center">
      <svg width="110" height="110" role="img" aria-label="Pale blue llama brand emblem"><rect width="110" height="110" rx="6" fill="var(--llama-blue)"/></svg>
      <div class="brand-name" style="font-size:20px;margin:10px 0 30px">Velmora Brew</div>
      <svg width="256" height="110" style="margin:0 -16px">
        <rect x="0" y="40" width="256" height="30" fill="var(--green)"/>
        <circle cx="128" cy="55" r="50" fill="#c9b35a"/>
        <circle cx="128" cy="55" r="40" fill="var(--green)"/>
      </svg>
    </div>
  </section>

</body>
</html>
```